Kelvor Engineers: Why you should hire us keepsake

New design. Open to plastic cards. We are an engineering firm that designs cell phone towers and commercial buildings. Please check out our website www.kelvorstruct.com for more details. We want people to remember our card and for it to be useful if possible. We want the same look and feel on these cards to be translated to other marketing material we may need such as brochures.

Target Market(s)

Architects, Developers and Telecommunication Carriers

Industry/Entity Type

Engineering

Contact Information for Business Card

Card with our company colors, logo, and innovative design with elements related to our industry.

Font styles to use
Sans Serif

Colors
9bcb3c
abd036
0255a3

Requirements
Must have
• Sleek and hip design
Nice to have
• Bright lime green and navy coloring that pops with an innovative design.
Should not have
• A basic and boring design

```html
<!DOCTYPE html>
<html lang="en">
<head>
<meta charset="utf-8">
<title>Kelvor Engineers – Business Card</title>
<link rel="stylesheet" href="https://fonts.googleapis.com/css2?family=Source+Sans+3:wght@400;600;700;900&display=swap">
<style>
  :root {
    --backdrop: #dfe5ec;
    --card: #f1f4f7;
    --card-edge: #d5dce4;
    --navy: #1d2748;
    --navy-band: #1a2540;
    --lime: #3be43b;
    --city-text: #c9ced8;
    --contact-text: #2a3350;
  }
  * { box-sizing: border-box; margin: 0; padding: 0; }
  html, body {
    width: 1200px; height: 900px; overflow: hidden;
    background: var(--backdrop);
    font-family: "Source Sans 3", Arial, sans-serif;
  }
  .card {
    position: absolute; left: 150px; top: 192px;
    width: 900px; height: 516px;
    background: var(--card);
    border: 1px solid var(--card-edge);
    border-radius: 16px;
    overflow: hidden;
    box-shadow: 0 10px 30px rgba(29, 39, 72, 0.12);
  }
  .brand-name {
    position: absolute; left: 42px; top: 44px;
    color: var(--lime);
    font-weight: 900;
    font-size: 64px; line-height: 60px;
    letter-spacing: -1px;
  }
  .tagline {
    position: absolute; right: 40px; top: 44px;
    color: var(--navy); font-weight: 600; font-size: 25px;
  }
  .person {
    position: absolute; right: 40px; top: 254px;
    color: var(--navy); font-weight: 600; font-size: 25px;
  }
  .contacts {
    position: absolute; right: 40px; top: 310px;
    list-style: none; text-align: right;
    color: var(--contact-text); font-size: 18px; line-height: 26px;
  }
  .contacts li { display: flex; justify-content: flex-end; align-items: center; gap: 6px; }
  .contacts svg { width: 15px; height: 15px; fill: var(--lime); flex: none; }
  .base-band {
    position: absolute; left: 0; right: 0; bottom: 0; height: 70px;
    background: var(--navy-band);
    border-top: 4px solid var(--lime);
    display: flex; align-items: center; padding-left: 190px;
    color: var(--city-text); font-size: 19px; letter-spacing: 0.3px;
  }
  .base-band .sep {
    display: inline-block; width: 2px; height: 20px;
    background: var(--lime); margin: 0 14px;
  }
</style>
</head>
<body>
  <section class="card" aria-label="Kelvor Engineers business card">
    <div class="brand-name">Kelvor<br>Engineers</div>
    <p class="tagline">Multi-discipline engineering</p>
    <p class="person">Dana Hollis Warren</p>
    <ul class="contacts">
      <li>555.014.2290
        <svg viewBox="0 0 16 16" aria-hidden="true"><path d="M3.5 1.5l2.5 0 1 3.5-1.7 1.2c.8 1.8 2.2 3.2 4 4l1.2-1.7 3.5 1v2.5c0 .8-.7 1.5-1.5 1.5C6.6 13.5 2 8.9 2 3c0-.8.7-1.5 1.5-1.5z"/></svg>
      </li>
      <li>555.017.4431
        <svg viewBox="0 0 16 16" aria-hidden="true"><path d="M4.5 0.5h7c.8 0 1.5.7 1.5 1.5v12c0 .8-.7 1.5-1.5 1.5h-7C3.7 15.5 3 14.8 3 14V2c0-.8.7-1.5 1.5-1.5zM5 2.5v9.5h6V2.5zM8 12.8a.9.9 0 100 1.8.9.9 0 000-1.8z"/></svg>
      </li>
      <li>dwarren@kelvorstruct.com
        <svg viewBox="0 0 16 16" aria-hidden="true"><path d="M1 3.5h14v9H1zM2 4.5v.4l6 4 6-4v-.4zm0 1.6V11.5h12V6.1L8 10z"/></svg>
      </li>
      <li>www.kelvorstruct.com
        <svg viewBox="0 0 16 16" aria-hidden="true"><path d="M8 1a7 7 0 100 14A7 7 0 008 1zm0 1.3c.8.8 1.5 2.1 1.8 3.7H6.2C6.5 4.4 7.2 3.1 8 2.3zM2.4 7h3.6c-.1.7-.1 1.3 0 2H2.4a5.8 5.8 0 010-2zm3.8 3h3.6c-.3 1.6-1 2.9-1.8 3.7-.8-.8-1.5-2.1-1.8-3.7zm4.8-3h2.6a5.8 5.8 0 010 2H11c.1-.7.1-1.3 0-2zM7 7h2c.1.7.1 1.3 0 2H7c-.1-.7-.1-1.3 0-2z"/></svg>
      </li>
    </ul>
    <div class="base-band">
      <span>ATLANTA</span><span class="sep"></span>
      <span>CHARLOTTE</span><span class="sep"></span>
      <span>HOUSTON</span><span class="sep"></span>
      <span>SAN ANTONIO</span>
    </div>
  </section>
</body>
</html>
```